2 Fold Brochure

We are a spa looking to create a professional elegant two fold brochure for a spa mainly black and white with a splash of lime green.
Look and feel: chic, modern, and spa-ish.

The front will include an image and also it should say: (somewhere under the photo) wherever you think it will look nice.
Skin Tightening
Cellulite Reduction
Body Contouring

The second Page:
Bipolar Radiofrequency(bolded): for immediate face lifting, tone and a complete new younger looking skin!
Multipolar Radiofrequency(bolded): with Vacuum system for body contour, cellulite and fat detachment from adipose tissue.
Cavitation with red LED to treat face and small areas of the body. Red LED light stimulates collagen synthesis.

Ultra Cavitation will sculpt, treat fat, cellulite and improve body shape! It does NOT involve surgery. There is no need for anesthesia, hospital stay or time off from work. Ultra cavitation will promote microscopic air bubbles to surround the lipocyte(fat cell) membranes and with its resonant frequency, the bubbles cause a high enough pressure to break up fat instantly. These broken lipocytes are then safely metabolized out of the human body.

PRESSOTHERAPY: A Complete Body Detox! Pressortherapy based on air pressure, promotes lymphatic drainage. It aslo has infrared system for body heat and electro muscle stimulation system.

Third Page:
Packages:

1. THE NEW FACELIFT:
*Skin Tightening
*Wrinkle Reduction
*Dark Circle Elimination
*Puffy Eye Relief

BODY SHAPING

2. BODY
*Fat Reduction
*Cellulite Reduction
*Body Firming

3. PRESSOTHERAPY (DETOX) $85
*Toxic Flushing
*Lymphatic Drainage
*Toning

5.POST PREGNANCY
*Fat Reduction
*Tummy Firming and Toning
*Cellulite Reduction
*Butt Toning

Buy 5 get 1 Free - $1,250
Buy 10 get 2 Free- $2,500

The back of the second page will include before and after photos I will be sending later. Also include the Logo in the front and by the prices. I have attached our logo.

Also we need a photo to place in the front. Something that shows face and body fat reduction.

Industry/Entity Type

Hospital

```html
<!DOCTYPE html>
<html lang="en">
<head>
<meta charset="utf-8">
<title>Luma Day Spa – Two Fold Brochure</title>
<link rel="stylesheet" href="https://fonts.googleapis.com/css2?family=Raleway:wght@400;500;600;700&display=swap">
<style>
  :root {
    --lime: #8cc63f;
    --green: #4a9e22;
    --deep-green: #1f6b12;
    --black: #111111;
    --ink: #2b2b2b;
    --grey-text: #6a6a6a;
    --paper: #ffffff;
    --mist: #ececec;
    --orange: #f08a1c;
    --stage: #ffffff;
  }
  * { box-sizing: border-box; margin: 0; padding: 0; }
  html, body { width: 1200px; height: 1000px; overflow: hidden; background: var(--stage); }
  body { font-family: "Raleway", Arial, sans-serif; color: var(--ink); position: relative; }

  .spread { position: absolute; left: 260px; display: flex; box-shadow: 0 10px 24px rgba(0,0,0,.12); }
  .spread--outside { top: 30px; }
  .spread--inside { top: 515px; }
  .page { position: relative; width: 340px; height: 455px; background: var(--paper); overflow: hidden; }

  .photo { position: absolute; }

  .brand { display: flex; align-items: center; gap: 7px; }
  .brand__dot { width: 14px; height: 14px; border-radius: 50%; background: var(--black); }
  .brand__name { font-weight: 700; font-size: 15px; color: var(--black); letter-spacing: .5px; }

  /* Page 4 – back cover */
  .back__band { position: absolute; right: 0; top: 0; width: 26px; height: 350px; background: var(--black); }
  .back__hero { left: 0; top: 0; width: 314px; height: 215px;
    background: linear-gradient(135deg, #d9b79a 0%, #c98f6b 40%, #f1e3d6 100%);
    border-top-right-radius: 150px 90px; }
  .back__curve { position: absolute; right: 0; top: 0; }
  .back__brand { position: absolute; left: 16px; top: 262px; }
  .price-list { position: absolute; left: 150px; top: 225px; width: 164px; background: var(--paper);
    padding: 8px 10px; list-style: none; border-left: 3px solid var(--lime); }
  .price-list li { font-size: 11.5px; font-weight: 500; line-height: 20px; color: var(--black); }
  .price-list .price { color: var(--green); font-weight: 600; }
  .back__strip { position: absolute; left: 0; bottom: 0; width: 100%; height: 105px; background: var(--black);
    display: flex; gap: 4px; padding: 10px 10px 12px; }
  .back__strip .photo { position: static; flex: 1; }
  .strip-a { background: linear-gradient(160deg, #9b7a66, #5d4a40); }
  .strip-b { background: linear-gradient(160deg, #7a4a2e, #c89070); }
  .strip-c { background: linear-gradient(160deg, #f3d8dc, #e79aa8 60%, #f7f0ee); }

  /* Page 1 – front cover */
  .front__edge { position: absolute; left: 0; top: 0; width: 12px; height: 100%; background: var(--black); }
  .front__edge2 { position: absolute; left: 12px; top: 0; width: 18px; height: 100%; background: var(--lime); }
  .front__header { position: absolute; left: 30px; top: 0; right: 0; height: 125px;
    background: linear-gradient(135deg, var(--lime) 0%, var(--green) 45%, var(--deep-green) 100%);
    padding: 26px 18px 0 0; text-align: right; color: var(--paper); }
  .front__header p { font-size: 15px; font-weight: 500; line-height: 26px; }
  .front__header strong { font-size: 21px; font-weight: 600; }
  .front__swoosh { position: absolute; left: 30px; top: 95px; }
  .front__flowers { left: 150px; top: 150px; width: 190px; height: 100px;
    background: radial-gradient(circle at 50% 55%, #f2a7a0 0%, #d9c3a3 35%, #f4f4f2 75%); }
  .front__brand { position: absolute; left: 42px; top: 168px; }
  .front__portrait { left: 30px; top: 255px; width: 310px; height: 175px;
    background: linear-gradient(160deg, #f6efe9 0%, #e9c7ad 35%, #4a2f24 75%, #e88a3a 100%); }

  /* Page 2 – treatments */
  .inner__edge { position: absolute; left: 0; top: 0; width: 16px; height: 100%; background: var(--black); }
  .inner__edge2 { position: absolute; left: 16px; top: 0; width: 24px; height: 100%; background: var(--lime); }
  .treat__photo { left: 95px; top: 8px; width: 200px; height: 72px;
    background: radial-gradient(ellipse at 60% 50%, #d99a55 0%, #8a6a50 40%, #ffffff 80%); }
  .treatments { position: absolute; left: 52px; top: 82px; right: 14px; }
  .treatment { position: relative; padding-left: 12px; margin-bottom: 8px; }
  .treatment::before { content: ""; position: absolute; left: 0; top: 3px;
    border-left: 7px solid var(--lime); border-top: 6px solid transparent; border-bottom: 6px solid transparent; }
  .treatment h2 { font-size: 11px; font-weight: 500; color: var(--black); line-height: 13px; text-transform: uppercase; }
  .treatment h2 b { display: block; color: var(--green); font-weight: 700; font-size: 12px; }
  .treatment p { font-size: 8.6px; line-height: 11.4px; color: var(--grey-text); margin-top: 4px; }
  .treatment p + p { margin-top: 6px; }

  /* Page 3 – packages */
  .pk__edge { position: absolute; left: 0; top: 0; width: 20px; height: 100%; background: var(--lime); }
  .pk__curve { position: absolute; right: 0; bottom: 0; }
  .package { position: absolute; }
  .package h3 { font-size: 12px; font-weight: 500; color: var(--black); }
  .package h3 b { font-weight: 600; color: var(--green); font-size: 14px; }
  .package ul { list-style: none; margin-top: 3px; }
  .package li { font-size: 8px; line-height: 11px; color: var(--grey-text); }
  .thumb { position: absolute; width: 66px; height: 66px; border-radius: 50%; border: 3px solid var(--paper);
    box-shadow: 3px 0 0 var(--lime); }
  .arrow { position: absolute; }
  .thumb--face { left: 30px; top: 14px; background: radial-gradient(circle, #f1d9c8, #cfa58a); }
  .thumb--body { left: 255px; top: 108px; background: linear-gradient(180deg, #e9e1e4, #5a2a4a 60%, #e9e1e4); }
  .thumb--detox { left: 30px; top: 205px; background: radial-gradient(circle, #f29a2e, #6a8a2a 60%, #3a5a1a); }
  .thumb--mother { left: 255px; top: 295px; background: linear-gradient(180deg, #f2c6cf, #d94a8a 55%, #e8d9c8); }
  .bundles { position: absolute; left: 118px; top: 380px; list-style: none; }
  .bundles li { font-size: 9px; font-weight: 700; color: var(--black); line-height: 12px; }
  .bundles .offer { color: var(--orange); }
  .bundles .free { color: var(--lime); }
</style>
</head>
<body>

<section class="spread spread--outside">
  <article class="page page--back">
    <div class="back__band"></div>
    <div class="photo back__hero" role="img" aria-label="Couple relaxing during a massage with candles and a flower"></div>
    <svg class="back__curve" width="60" height="220" viewBox="0 0 60 220" aria-hidden="true">
      <path d="M0 0 Q55 40 58 220 L60 220 L60 0 Z" fill="#8cc63f"/>
    </svg>
    <div class="brand back__brand"><span class="brand__dot"></span><span class="brand__name">Luma Day Spa</span></div>
    <ul class="price-list">
      <li>The New Facelift <span class="price">- $109</span></li>
      <li>Body Shaping <span class="price">- $220</span></li>
      <li>The New Facelift <span class="price">- $100</span></li>
      <li>The New Facelift <span class="price">- $300</span></li>
    </ul>
    <div class="back__strip">
      <div class="photo strip-a" role="img" aria-label="Before and after facial treatment"></div>
      <div class="photo strip-b" role="img" aria-label="Back massage"></div>
      <div class="photo strip-c" role="img" aria-label="Feet among rose petals"></div>
    </div>
  </article>

  <article class="page page--front">
    <div class="front__edge"></div>
    <div class="front__edge2"></div>
    <header class="front__header">
      <p>Skin <strong>Tightening</strong></p>
      <p>Cellulite <strong>Reduction</strong></p>
      <p><strong>Body</strong> Contouring</p>
    </header>
    <svg class="front__swoosh" width="310" height="80" viewBox="0 0 310 80" aria-hidden="true">
      <path d="M0 30 Q150 0 310 20 L310 60 Q150 30 0 80 Z" fill="#111111"/>
      <path d="M0 30 Q150 0 310 20 L310 26 Q150 8 0 38 Z" fill="#8cc63f"/>
    </svg>
    <div class="photo front__flowers" role="img" aria-label="Spa stones, towel and pink lilies"></div>
    <div class="brand front__brand"><span class="brand__dot"></span><span class="brand__name">Luma Day Spa</span></div>
    <div class="photo front__portrait" role="img" aria-label="Woman receiving a facial massage with orange flowers in her hair"></div>
  </article>
</section>

<section class="spread spread--inside">
  <article class="page page--treatments">
    <div class="inner__edge"></div>
    <div class="inner__edge2"></div>
    <div class="photo treat__photo" role="img" aria-label="Spa stones, daisies and a starfish"></div>
    <div class="treatments">
      <section class="treatment">
        <h2>Bipolar <b>Radiofrequency</b></h2>
        <p>for immediate face lifting, tone and a complete new younger looking skin!</p>
      </section>
      <section class="treatment">
        <h2>Multipolar <b>Radiofrequency</b></h2>
        <p>with Vacuum system for body contour, cellulite and fat detachment from adipose tissue.<br>Cavitation with red LED to treat face and small areas of the body. Red LED light stimulates collagen synthesis.</p>
        <p>Ultra Cavitation will sculpt, treat fat, cellulite and improve body shape! It does NOT involve surgery. There is no need for anesthesia, hospital stay or time off from work. Ultra cavitation will promote microscopic air bubbles to surround the lipocyte(fat cell) membranes and with its resonant frequency, the bubbles cause high enough pressure to break up fat instantly. These broken lipocytes are then safely metabolized out of the human body.</p>
      </section>
      <section class="treatment">
        <h2><b>Pressotherapy</b></h2>
        <p>A Complete Body Detox! Pressortherapy based on air pressure, promotes lymphatic drainage. It also has infrared system for body heat and electro muscle stimulation system.</p>
      </section>
    </div>
  </article>

  <article class="page page--packages">
    <div class="pk__edge"></div>
    <svg class="pk__curve" width="120" height="260" viewBox="0 0 120 260" aria-hidden="true">
      <path d="M120 0 Q110 190 0 260 L120 260 Z" fill="#ececec"/>
    </svg>

    <div class="photo thumb thumb--face" role="img" aria-label="Woman with smooth skin"></div>
    <svg class="arrow" style="left:104px;top:40px" width="18" height="16" viewBox="0 0 18 16" aria-hidden="true"><path d="M2 2 Q2 10 10 10 L10 6 L16 11 L10 15 L10 12 Q0 12 2 2 Z" fill="#8cc63f"/></svg>
    <div class="package" style="left:126px;top:22px">
      <h3>The New <b>Facelift</b></h3>
      <ul><li>Skin Tightening</li><li>Wrinkle Reduction</li><li>Dark Circle Elimination</li><li>Puffy Eye Relief</li></ul>
    </div>

    <div class="package" style="left:44px;top:112px">
      <h3>Body <b>Shaping</b></h3>
      <ul><li>Fat Reduction</li><li>Cellulite Reduction</li><li>Body Firming</li></ul>
    </div>
    <svg class="arrow" style="left:232px;top:134px" width="18" height="16" viewBox="0 0 18 16" aria-hidden="true"><path d="M16 2 Q16 10 8 10 L8 6 L2 11 L8 15 L8 12 Q18 12 16 2 Z" fill="#8cc63f"/></svg>
    <div class="photo thumb thumb--body" role="img" aria-label="Woman in shaping bodysuit"></div>

    <div class="photo thumb thumb--detox" role="img" aria-label="Detox juices and fruit"></div>
    <svg class="arrow" style="left:104px;top:230px" width="18" height="16" viewBox="0 0 18 16" aria-hidden="true"><path d="M2 2 Q2 10 10 10 L10 6 L16 11 L10 15 L10 12 Q0 12 2 2 Z" fill="#8cc63f"/></svg>
    <div class="package" style="left:126px;top:212px">
      <h3>Pressotherapy <b style="font-size:12px">(Detox)</b> $85</h3>
      <ul><li>Toxic Flushing</li><li>Lymphatic Drainage</li><li>Toning</li></ul>
    </div>

    <div class="package" style="left:44px;top:296px">
      <h3>Post <b>Pregnancy</b></h3>
      <ul><li>Fat Reduction</li><li>Tummy Firming and Toning</li><li>Cellulite Reduction</li><li>Butt Toning</li></ul>
    </div>
    <svg class="arrow" style="left:232px;top:320px" width="18" height="16" viewBox="0 0 18 16" aria-hidden="true"><path d="M16 2 Q16 10 8 10 L8 6 L2 11 L8 15 L8 12 Q18 12 16 2 Z" fill="#8cc63f"/></svg>
    <div class="photo thumb thumb--mother" role="img" aria-label="Mother holding her baby"></div>

    <ul class="bundles" style="left:44px">
      <li><span class="offer">BUY 5 GET 1</span> <span class="free">FREE</span> - $1,250</li>
      <li><span class="offer">BUY 10 GET 2</span> <span class="free">FREE</span> - $2,500</li>
    </ul>
  </article>
</section>

</body>
</html>
```